Luxury free range egg pack for eggs with golden orange yolks

We are looking for a new faced egg pack for one of our brands called Meadow Crest which is free range eggs with golden yolks.
This will be for a more up market target audience.

Target Market(s)

Luxury egg purchase

Industry/Entity Type

Egg production

Font styles to use
Decorative
Script

Colors
F0912C
F2A743
F7CA91
FBE8D2
FDF5EE

Requirements
Must have
• Orange or gold colouring in place in the theme

```html
<!DOCTYPE html>
<html lang="en">
<head>
<meta charset="utf-8">
<title>Meadow Crest Free Range Egg Packaging</title>
<link rel="stylesheet" href="https://fonts.googleapis.com/css2?family=Yesteryear&family=Kaushan+Script&family=Cinzel:wght@700&family=Archivo:wght@700;800&display=swap">
<style>
  :root {
    --bg-top: #f8c3a2;
    --bg-bottom: #c2592a;
    --orange: #f0912c;
    --amber: #f2a743;
    --apricot: #f7ca91;
    --cream: #fbe8d2;
    --ivory: #fdf5ee;
    --copper: #b4622c;
    --brown: #7a3514;
    --gold-light: #fff2a8;
    --gold: #e2b33c;
    --gold-dark: #9a6a12;
    --label-light: #e9b48d;
    --label-dark: #c9875d;
  }
  * { box-sizing: border-box; margin: 0; padding: 0; }
  html, body { width: 1200px; height: 576px; overflow: hidden; }
  body {
    background: linear-gradient(180deg, var(--bg-top) 0%, #e5946a 55%, var(--bg-bottom) 100%);
    font-family: "Archivo", sans-serif;
    position: relative;
  }

  /* shared pieces */
  .brand-badge {
    position: absolute;
    display: flex; align-items: center; justify-content: center; gap: 5px;
    font-family: "Archivo", sans-serif; font-weight: 800;
    color: var(--brown); white-space: nowrap;
  }
  .brand-badge .dot { width: 9px; height: 9px; border-radius: 50%; background: var(--orange); }
  .product-title {
    position: absolute; left: 0; right: 0; text-align: center;
    font-family: "Yesteryear", cursive;
    background: linear-gradient(180deg, var(--gold-light) 0%, var(--gold) 45%, var(--gold-dark) 100%);
    -webkit-background-clip: text; background-clip: text; color: transparent;
    filter: drop-shadow(1px 2px 1px rgba(90,40,10,.45));
  }
  .tagline {
    position: absolute;
    border-radius: 14px;
    background: linear-gradient(180deg, #fffbd0 0%, #f7dc72 60%, #d9ae3c 100%);
    font-family: "Kaushan Script", cursive;
    color: var(--brown); text-align: center; white-space: nowrap;
  }
  .code-strip {
    position: absolute; display: flex; align-items: center; justify-content: center; gap: 6px;
    font-family: "Archivo", sans-serif; font-weight: 700; color: var(--brown); white-space: nowrap;
  }
  .code-strip .sep { width: 6px; height: 6px; border-radius: 50%; background: var(--copper); }
  .corner-egg {
    position: absolute; width: 34px; height: 44px; border-radius: 50% 50% 50% 50% / 58% 58% 42% 42%;
    background: radial-gradient(circle at 45% 40%, #e9c3a8 0%, #c99070 70%, #b37756 100%);
  }

  /* carton lid label */
  .carton-label {
    position: absolute; left: 40px; top: 160px; width: 560px; height: 256px;
    background: radial-gradient(ellipse at 65% 30%, #f8dcc6 0%, var(--label-light) 35%, var(--label-dark) 100%);
    border: 3px solid var(--copper);
    box-shadow: inset 0 0 0 5px #dca27a, inset 0 0 0 7px #9c5a30;
  }
  .carton-label .brand-badge { left: 0; right: 0; top: 34px; font-size: 17px; }
  .carton-label .product-title { top: 78px; font-size: 66px; }
  .carton-label .grade-row {
    position: absolute; left: 0; right: 0; top: 166px;
    display: flex; align-items: center; justify-content: center; gap: 10px;
  }
  .carton-label .grade {
    font-family: "Cinzel", serif; font-size: 13px; color: #8a4a26;
  }
  .carton-label .count {
    font-family: "Cinzel", serif; font-size: 18px; color: var(--ivory);
    text-shadow: 1px 1px 1px rgba(90,40,10,.5);
  }
  .carton-label .count small { font-size: 10px; }
  .carton-label .tagline { position: static; padding: 3px 16px; font-size: 17px; }
  .carton-label .code-bar {
    position: absolute; left: 10px; right: 10px; bottom: 12px; height: 24px;
    background: linear-gradient(180deg, #fff6c8, #f0cd62 70%, #cfa23c);
  }
  .carton-label .code-strip { inset: 0; font-size: 11px; }
  .carton-label .corner-egg.tl { left: 20px; top: 18px; }
  .carton-label .corner-egg.tr { right: 20px; top: 18px; }
  .carton-label .corner-egg.bl { left: 20px; bottom: 48px; }
  .carton-label .corner-egg.br { right: 20px; bottom: 48px; }

  /* shipping box side panel */
  .box-panel {
    position: absolute; left: 640px; top: 118px; width: 520px; height: 340px;
    background: radial-gradient(ellipse at 55% 40%, var(--ivory) 0%, var(--cream) 55%, #f3ceb2 100%);
    border: 2px solid var(--gold);
    box-shadow: inset 0 0 0 4px var(--ivory), inset 0 0 0 5px #e8c27a;
  }
  .box-panel .care-band {
    position: absolute; left: 0; right: 0; top: 14px; text-align: center;
    font-family: "Cinzel", serif; font-size: 20px; letter-spacing: 2px; color: #8a3a12;
  }
  .box-panel .storage-note {
    position: absolute; left: 26px; top: 52px; width: 170px;
    font-size: 9.5px; font-weight: 800; line-height: 1.35; color: var(--brown);
  }
  .box-panel .brand-badge { left: 0; right: 0; top: 110px; font-size: 16px; }
  .box-panel .product-title { top: 138px; font-size: 58px; }
  .box-panel .tagline { left: 50%; transform: translateX(-50%); top: 214px; padding: 3px 16px; font-size: 15px; }
  .box-panel .code-strip { left: 0; right: 0; top: 258px; font-size: 10px; }
  .box-panel .pack-size {
    position: absolute; right: 30px; bottom: 26px; text-align: right;
    font-family: "Cinzel", serif; color: #4a2410;
  }
  .box-panel .pack-size .grade { display: block; font-size: 9px; }
  .box-panel .pack-size .qty { font-size: 17px; }
  .box-panel .corner-egg.tl { left: 22px; top: 118px; }
  .box-panel .corner-egg.tr { right: 22px; top: 50px; }
  .box-panel .corner-egg.bl { left: 22px; bottom: 22px; }
  .box-panel .corner-egg.mr { right: 22px; top: 160px; }
</style>
</head>
<body>

  <section class="carton-label" aria-label="Egg carton lid label">
    <div class="corner-egg tl" role="img" aria-label="Decorative patterned egg"></div>
    <div class="corner-egg tr" role="img" aria-label="Decorative patterned egg"></div>
    <div class="corner-egg bl" role="img" aria-label="Decorative patterned egg"></div>
    <div class="corner-egg br" role="img" aria-label="Decorative patterned egg"></div>

    <div class="brand-badge"><span class="dot"></span>Meadow Crest</div>
    <h1 class="product-title">Free Range Egg</h1>
    <div class="grade-row">
      <span class="grade">Class A</span>
      <span class="tagline">With Golden Orange Yolks</span>
      <span class="count">6 <small>Large Egg</small></span>
    </div>
    <div class="code-bar">
      <div class="code-strip">
        <span>0 = ORGANIC</span><span class="sep"></span>
        <span>1 = F/RANGE</span><span class="sep"></span>
        <span>2 = BARN</span><span class="sep"></span>
        <span>3 = CAGE</span>
      </div>
    </div>
  </section>

  <section class="box-panel" aria-label="Shipping box side panel">
    <div class="corner-egg tl" role="img" aria-label="Decorative patterned egg"></div>
    <div class="corner-egg tr" role="img" aria-label="Decorative patterned egg"></div>
    <div class="corner-egg mr" role="img" aria-label="Decorative patterned egg"></div>
    <div class="corner-egg bl" role="img" aria-label="Decorative patterned egg"></div>

    <div class="care-band">HANDLE WITH CARE</div>
    <p class="storage-note">KEEP REFRIGERATED AFTER PURCHASE OR STORE IN A COOL DRY PLACE</p>
    <div class="brand-badge"><span class="dot"></span>Meadow Crest</div>
    <h2 class="product-title">Free Range Egg</h2>
    <div class="tagline">With Golden Orange Yolks</div>
    <div class="code-strip">
      <span>0 = ORGANIC</span><span class="sep"></span>
      <span>1 = F/RANGE</span><span class="sep"></span>
      <span>2 = BARN</span><span class="sep"></span>
      <span>3 = CAGE</span>
    </div>
    <div class="pack-size"><span class="grade">Class A</span><span class="qty">5 Dozzen</span></div>
  </section>

</body>
</html>
```